Property management company looking for modern card design

We at Blue Heron Partners provides property management services for its residential and commercial properties, with expertise in all categories of multifamily, industrial and office projects throughout California.

We need a business card design that is professional and modern designed business card. In our field, clients get hundreds of business cards, we would like our card to stand out.

Please avoid small print.

Target Market(s)

Professionals and high end clients

Industry/Entity Type

Financial Planning

Contact Information for Business Card

Company Name: Blue Heron Partners, Name, email, license #, phone number, website blueheronpartners.com

Font styles to use
Sans Serif

Requirements
Must have
• The card design needs to be adaptable because there is a possibly we will be expanding into different sectors other than real estate. The card design should be focused on financial planning and asset management.
Nice to have
• Modern and simple business card. Eye catching. Non-standard size/shaped cards would be great.
• blueheronpartners.com
Should not have
• Too many bright color or any pictures or shapes of real estate stuff.

```html
<!DOCTYPE html>
<html lang="en">
<head>
<meta charset="utf-8">
<title>Blue Heron Partners – Business Card</title>
<link rel="stylesheet" href="https://fonts.googleapis.com/css2?family=Ubuntu:wght@400;500;700&family=Arimo:wght@700&display=swap">
<style>
  :root {
    --stage: #e4e1d8;
    --kraft: #c9a977;
    --brand-red: #a80000;
    --ink: #272b30;
    --web-grey: #45464a;
  }
  * { margin: 0; padding: 0; box-sizing: border-box; }
  html, body { width: 900px; height: 1200px; overflow: hidden; }
  body {
    background: var(--stage);
    position: relative;
    font-family: "Ubuntu", sans-serif;
  }
  .card {
    position: absolute;
    background: var(--kraft);
    overflow: hidden;
  }
  .card > * { position: absolute; }
  .bar { background: var(--brand-red); }
  .brand-dot {
    width: 40px; height: 40px;
    border-radius: 50%;
    background: var(--brand-red);
  }
  .brand-name {
    color: var(--brand-red);
    font-weight: 500;
    font-size: 26px;
    letter-spacing: 4px;
    white-space: nowrap;
    text-align: center;
    line-height: 1;
  }
  .website {
    font-family: "Arimo", sans-serif;
    font-weight: 700;
    font-size: 17px;
    color: var(--web-grey);
    line-height: 1;
    white-space: nowrap;
  }

  /* Front: portrait card */
  .card--front { left: 313px; top: 141px; width: 300px; height: 527px; }
  .card--front .brand-dot { left: 131px; top: 93px; }
  .card--front .brand-name { left: 0; width: 300px; top: 173px; }
  .card--front .bar--top { left: 158px; top: 239px; width: 116px; height: 15px; }
  .card--front .holder-name {
    right: 26px; top: 261px;
    font-size: 30px; font-weight: 500; color: var(--ink);
    line-height: 1; white-space: nowrap;
  }
  .card--front .holder-role {
    right: 31px; top: 298px;
    font-size: 13px; color: var(--ink); line-height: 1;
  }
  .card--front .bar--block { left: 158px; top: 322px; width: 116px; height: 92px; }
  .card--front .contact {
    right: 31px; top: 417px;
    list-style: none; text-align: right;
    font-size: 12px; font-weight: 700; color: var(--ink);
    line-height: 22px; white-space: nowrap;
  }
  .card--front .bar--thin { left: 158px; top: 479px; width: 116px; height: 6px; }
  .card--front .website { right: 33px; top: 487px; }
  .card--front .bar--foot { left: 158px; top: 509px; width: 116px; height: 18px; }

  /* Back: landscape card */
  .card--back { left: 186px; top: 723px; width: 527px; height: 300px; }
  .card--back .bar--top { left: 0; top: 36px; width: 100%; height: 17px; }
  .card--back .brand-dot { left: 244px; top: 104px; }
  .card--back .brand-name { left: 0; width: 527px; top: 190px; }
  .card--back .website { left: 0; width: 527px; text-align: center; top: 254px; }
  .card--back .bar--foot { left: 0; top: 277px; width: 100%; height: 6px; }
</style>
</head>
<body>
  <section class="card card--front" aria-label="Business card front">
    <span class="brand-dot" aria-hidden="true"></span>
    <p class="brand-name">Blue Heron</p>
    <span class="bar bar--top"></span>
    <h1 class="holder-name">Mark Ellison</h1>
    <p class="holder-role">managing director</p>
    <span class="bar bar--block"></span>
    <ul class="contact">
      <li>mark.ellison@blueheronpartners.com</li>
      <li>555-555-5555</li>
      <li>License Nr:000001</li>
    </ul>
    <span class="bar bar--thin"></span>
    <p class="website">blueheronpartners.com</p>
    <span class="bar bar--foot"></span>
  </section>

  <section class="card card--back" aria-label="Business card back">
    <span class="bar bar--top"></span>
    <span class="brand-dot" aria-hidden="true"></span>
    <p class="brand-name">Blue Heron</p>
    <p class="website">blueheronpartners.com</p>
    <span class="bar bar--foot"></span>
  </section>
</body>
</html>
```